Real Estate Company Looking for Business Card Designs for 3 Executives

Hello!
Thanks so much for considering our project! We are a real estate investment company located in Edmonton, Alberta called Bellhaven Group of Companies. We invest/develop both commercial and residential real estate and are looking to create 3 DOUBLE-SIDED business cards for 3 top executives in the company! (for some reason it won't let us select the double-sided option, but yes, the cards are double sided and would be happy to tip extra)

We have certain guidelines that we want our business cards to for sure follow - the back of the Business card has to be the Black Background Version of the Logo which has already been designed and linked as a file (first file). We want the entire back of the card to simply just be the black background logo. In terms of the front of the card, would like to see a smaller version of the white background logo (linked as the second file) in the top left hand corner - of course, feel free to get creative and we can make revisions together along the way! and Then after that, just text. We want the card to be sharp, clean, easy on the eyes and highly professional looking. We would like the card to include the Full name of the Company (Bellhaven Group of Companies), Name of the Person, Title, Phone, Email. If possible please provide the front part of the card for 3 people:

1) Bellhaven Group of Companies, Liora Quenby, Chief Financial Officer, 780-555-0142, lioraquenby@bellhavengroup.example

2) Bellhaven Group of Companies, Tobias Quenby, Chief Executive Officer, 780-555-0187, tobiasquenby@bellhavengroup.example

3) Bellhaven Group of Companies, Rui Delcourt, Chief Operations Officer, 587-555-0163, ruidelcourt@bellhavengroup.example

Thank you so much for considering our project & we look forward to seeing your designs!

```html
<!DOCTYPE html>
<html lang="en">
<head>
<meta charset="utf-8">
<title>Bellhaven Group of Companies – Business Cards</title>
<link rel="stylesheet" href="https://fonts.googleapis.com/css2?family=Arimo:wght@400;700&display=swap">
<style>
  :root {
    --page-bg: #c9c9c9;
    --card-black: #141414;
    --card-black-soft: #1c1c1c;
    --ink-white: #f4f6f7;
    --ink-muted: #b9bcbe;
    --rule-grey: #4a4a4a;
    --pattern-dark: #0c0c0c;
    --pattern-light: #2a2a2a;
  }
  * { box-sizing: border-box; margin: 0; padding: 0; }
  html, body { width: 1200px; height: 800px; overflow: hidden; }
  body {
    background: var(--page-bg);
    font-family: "Arimo", Arial, sans-serif;
    color: var(--ink-white);
    display: grid;
    grid-template-columns: 560px 560px;
    grid-template-rows: 320px 320px;
    gap: 24px;
    justify-content: center;
    align-content: center;
  }
  .card {
    position: relative;
    width: 560px;
    height: 320px;
    background: var(--card-black);
    overflow: hidden;
  }

  /* Front */
  .card-front { background: var(--card-black-soft); }
  .brand-lockup {
    display: flex;
    align-items: center;
    gap: 12px;
  }
  .front-brand {
    position: absolute;
    top: 36px;
    left: 36px;
  }
  .brand-mark {
    width: 14px;
    height: 14px;
    background: var(--ink-white);
  }
  .brand-name {
    font-size: 24px;
    font-weight: 400;
    letter-spacing: 0.42em;
    color: var(--ink-white);
  }
  .company-name {
    position: absolute;
    top: 76px;
    left: 36px;
    font-size: 12px;
    letter-spacing: 0.18em;
    text-transform: uppercase;
    color: var(--ink-muted);
  }
  .front-rule {
    position: absolute;
    left: 36px;
    right: 36px;
    top: 150px;
    height: 1px;
    background: var(--rule-grey);
  }
  .person {
    position: absolute;
    left: 36px;
    bottom: 30px;
  }
  .person-name {
    font-size: 21px;
    font-weight: 700;
    letter-spacing: 0.02em;
    text-transform: uppercase;
    line-height: 1.1;
  }
  .person-title {
    font-size: 15px;
    line-height: 1.25;
    margin-bottom: 10px;
  }
  .person-rule {
    width: 220px;
    height: 1px;
    background: var(--rule-grey);
    margin-bottom: 9px;
  }
  .contact-line {
    display: flex;
    align-items: center;
    gap: 7px;
    font-size: 15px;
    line-height: 1.4;
    white-space: nowrap;
  }
  .contact-line svg { width: 13px; height: 13px; flex: none; }
  .website {
    position: absolute;
    right: 36px;
    bottom: 55px;
    font-size: 15px;
    line-height: 1.4;
  }

  /* Back */
  .back-pattern {
    position: absolute;
    inset: 0;
    background: linear-gradient(135deg, var(--pattern-light) 0%, var(--pattern-dark) 45%, var(--pattern-light) 75%, var(--pattern-dark) 100%);
  }
  .back-brand {
    position: absolute;
    left: 0;
    right: 0;
    top: 50%;
    transform: translateY(-50%);
    justify-content: center;
    gap: 14px;
  }
  .back-brand .brand-name { font-size: 26px; }
</style>
</head>
<body>
  <section class="card card-front" aria-label="Business card front – Liora Quenby">
    <div class="brand-lockup front-brand"><span class="brand-mark"></span><span class="brand-name">BELLHAVEN</span></div>
    <p class="company-name">Bellhaven Group of Companies</p>
    <div class="front-rule"></div>
    <div class="person">
      <p class="person-name">Liora Quenby</p>
      <p class="person-title">Chief Financial Officer</p>
      <div class="person-rule"></div>
      <p class="contact-line"><svg viewBox="0 0 16 16" aria-hidden="true"><path fill="#f4f6f7" d="M3.6 1.5l2.2 2.6-1.3 1.6c.9 2 2.8 3.9 4.8 4.8l1.6-1.3 2.6 2.2-1.3 2.1C7.1 15 1 8.9 1.5 3z"/></svg>780-555-0142</p>
      <p class="contact-line"><svg viewBox="0 0 16 16" aria-hidden="true"><rect x="1" y="3" width="14" height="10" fill="#f4f6f7"/><path d="M1 3l7 5.5L15 3" fill="none" stroke="#1c1c1c" stroke-width="1.3"/></svg>lioraquenby@bellhavengroup.example</p>
    </div>
    <p class="website">www.bellhavengroup.example</p>
  </section>

  <section class="card card-front" aria-label="Business card front – Tobias Quenby">
    <div class="brand-lockup front-brand"><span class="brand-mark"></span><span class="brand-name">BELLHAVEN</span></div>
    <p class="company-name">Bellhaven Group of Companies</p>
    <div class="front-rule"></div>
    <div class="person">
      <p class="person-name">Tobias Quenby</p>
      <p class="person-title">Chief Executive Officer</p>
      <div class="person-rule"></div>
      <p class="contact-line"><svg viewBox="0 0 16 16" aria-hidden="true"><path fill="#f4f6f7" d="M3.6 1.5l2.2 2.6-1.3 1.6c.9 2 2.8 3.9 4.8 4.8l1.6-1.3 2.6 2.2-1.3 2.1C7.1 15 1 8.9 1.5 3z"/></svg>780-555-0187</p>
      <p class="contact-line"><svg viewBox="0 0 16 16" aria-hidden="true"><rect x="1" y="3" width="14" height="10" fill="#f4f6f7"/><path d="M1 3l7 5.5L15 3" fill="none" stroke="#1c1c1c" stroke-width="1.3"/></svg>tobiasquenby@bellhavengroup.example</p>
    </div>
    <p class="website">www.bellhavengroup.example</p>
  </section>

  <section class="card card-front" aria-label="Business card front – Rui Delcourt">
    <div class="brand-lockup front-brand"><span class="brand-mark"></span><span class="brand-name">BELLHAVEN</span></div>
    <p class="company-name">Bellhaven Group of Companies</p>
    <div class="front-rule"></div>
    <div class="person">
      <p class="person-name">Rui Delcourt</p>
      <p class="person-title">Chief Operations Officer</p>
      <div class="person-rule"></div>
      <p class="contact-line"><svg viewBox="0 0 16 16" aria-hidden="true"><path fill="#f4f6f7" d="M3.6 1.5l2.2 2.6-1.3 1.6c.9 2 2.8 3.9 4.8 4.8l1.6-1.3 2.6 2.2-1.3 2.1C7.1 15 1 8.9 1.5 3z"/></svg>587-555-0163</p>
      <p class="contact-line"><svg viewBox="0 0 16 16" aria-hidden="true"><rect x="1" y="3" width="14" height="10" fill="#f4f6f7"/><path d="M1 3l7 5.5L15 3" fill="none" stroke="#1c1c1c" stroke-width="1.3"/></svg>ruidelcourt@bellhavengroup.example</p>
    </div>
    <p class="website">www.bellhavengroup.example</p>
  </section>

  <section class="card card-back" aria-label="Business card back">
    <div class="back-pattern" role="img" aria-label="Glossy black repeating brand pattern background"></div>
    <div class="brand-lockup back-brand"><span class="brand-mark"></span><span class="brand-name">BELLHAVEN</span></div>
  </section>
</body>
</html>
```